Webdesign für Kleingruppenreisen in die Südsteiermark
Zielgruppe
Wir sind ein Start-Up Unternehmen, das als Kleingruppenreisen in die Südsteiermark veranstaltet; der Schwerpunkt liegt auf dem Kulinarischen. Zielgruppe sind Geschäftsleute, die diese Kurzreisen (Do-So) für Marketingzwecke oder als Mitarbeiterbonus (oder auch privat) nutzen möchten.
Aufgabenstellung
Die Homepage soll eine Online-Shop Möglichkeit bieten, in der die Reise (bisher gibt es nur einen Ablauf) gebucht werden kann. Optisch sollte sie sich an das bereits von Ihnen erstellte Logo anlehnen und möglichst ansprechende Fotos von der Südsteiermark, Graz, Leoben usw. enthalten. (Siehe die beiden Flyer und das Logo)
Wir haben inzwischen Bildfreigaben von Haldauer und dem Tourismusverband Kellwinden erhalten und können auch eigene Bilder zur Verfügung stellen. Bitte kontaktieren Sie uns dafür, wenn nötig.

```html
<!DOCTYPE html>
<html lang="de">
<head>
<meta charset="utf-8">
<title>Genussfahrten – Kulinarische Kleingruppenreisen</title>
<link href="https://fonts.googleapis.com/css2?family=Montserrat:wght@400;500;600;700;800&family=Lora:wght@400&display=swap" rel="stylesheet">
<style>
:root{
  --green:#3d6b0a;
  --green-dark:#356008;
  --green-text:#4a7a12;
  --ink:#3b3b3b;
  --muted:#8a8a8a;
  --paper:#f6f5f1;
  --panel:#efefef;
  --line:#e6e6e6;
  --white:#ffffff;
}
*{margin:0;padding:0;box-sizing:border-box}
html,body{width:1200px;height:3255px;overflow:hidden}
body{font-family:'Montserrat',sans-serif;color:var(--ink);background:var(--white);position:relative}
.abs{position:absolute}

/* header */
.site-header{position:absolute;left:0;top:0;width:1200px;height:88px;background:var(--white);box-shadow:0 2px 6px rgba(0,0,0,.12);z-index:2}
.brand{position:absolute;left:64px;top:28px;display:flex;align-items:center;gap:8px;font-weight:700;font-size:20px;color:var(--green)}
.brand-dot{width:14px;height:14px;border-radius:50%;background:var(--green)}
.main-nav{position:absolute;right:126px;top:46px;display:flex;gap:18px;font-size:15px;letter-spacing:4.2px;font-weight:600;color:var(--green)}
.main-nav span.sep{letter-spacing:0}
.social-top{position:absolute;right:126px;top:20px;display:flex;gap:16px}
.social-top i,.social-foot i{display:block;width:10px;height:10px;border-radius:50%;background:var(--green)}

/* hero */
.hero{position:absolute;left:0;top:88px;width:1200px;height:587px;background:linear-gradient(180deg,#b99a5e 0%,#8b8a4a 30%,#4d6a23 60%,#2f4a14 100%)}
.hero-title{position:absolute;left:0;width:1200px;top:240px;text-align:center;font-size:70px;font-weight:500;letter-spacing:4px;color:var(--white)}
.hero-rule{position:absolute;left:517px;top:350px;width:166px;height:1px;background:rgba(255,255,255,.7)}
.hero-text{position:absolute;left:380px;width:440px;top:387px;text-align:center;color:var(--white);font-size:14px;line-height:18px;letter-spacing:1.2px}
.hero-btn{position:absolute;left:525px;top:497px;width:150px;height:36px;border:1px dashed rgba(255,255,255,.6);background:rgba(0,0,0,.15);color:var(--white);font-size:10px;font-weight:700;letter-spacing:3px;text-align:center;line-height:36px}
.hero-badge{position:absolute;left:560px;top:648px;width:80px;height:72px;z-index:1}

/* about */
.about{position:absolute;left:0;top:675px;width:1200px;height:570px;background:var(--paper)}
.about h2{position:absolute;left:175px;width:380px;top:68px;text-align:center;font-weight:400;font-size:36px}
.kicker{font-size:10px;font-weight:600;letter-spacing:1.5px;color:var(--green);text-align:center}
.about .kicker{position:absolute;left:175px;width:380px;top:117px}
.about-text{position:absolute;left:175px;width:380px;top:154px;text-align:center;font-size:10.5px;line-height:18px;letter-spacing:.9px;color:#444}
.about-text p{margin-bottom:18px}
.collage{position:absolute;left:607px;top:89px;width:459px;height:391px}
.tile{position:absolute;width:222px;height:188px;border:5px solid var(--white);outline:1px solid rgba(0,0,0,.1)}
.tile.a{left:0;top:0;background:linear-gradient(135deg,#5d7a2e,#2d3a2a)}
.tile.b{left:237px;top:0;background:linear-gradient(135deg,#6aa02a,#7a1d1d)}
.tile.c{left:0;top:203px;background:linear-gradient(135deg,#b79d8c,#6b1417)}
.tile.d{left:237px;top:203px;background:linear-gradient(135deg,#4b6e1d,#a9c25a)}
.tastes{position:absolute;left:152px;top:125px;width:150px;height:140px;border-radius:40%;background:var(--paper);text-align:center;font-family:'Lora',serif;font-size:20px;line-height:28px;letter-spacing:1.5px;color:var(--green);padding-top:42px}

/* collections */
.collection-banner{position:absolute;left:127px;top:1246px;width:648px;height:388px;background:linear-gradient(135deg,#5a9a1f 0%,#7cae3a 45%,#b49868 80%,#c9a877 100%)}
.banner-title{position:absolute;left:52px;top:102px;color:var(--white);font-weight:800;font-size:50px;line-height:56px}
.banner-title small{font-size:32px;font-weight:700}
.banner-sub{position:absolute;left:57px;top:220px;color:var(--white);font-size:13px}
.btn-green{position:absolute;background:var(--green);color:var(--white);font-weight:700;font-size:9px;letter-spacing:1.5px;text-align:center}
.banner-btn{left:57px;top:265px;width:88px;height:31px;line-height:31px}
.collection-list{position:absolute;left:775px;top:1246px;width:298px;height:388px}
.collection-item{height:97px;background:var(--panel);border-bottom:1px solid #e2e2e2;padding:30px 0 0 30px;font-size:13px;line-height:16px;color:#444;position:relative}
.collection-item.active{background:var(--green-dark);color:var(--white)}
.collection-item.active::before{content:"";position:absolute;left:-16px;top:32px;border-right:16px solid var(--green-dark);border-top:16px solid transparent;border-bottom:16px solid transparent}
.collection-item .num{position:absolute;left:82px;top:6px;font-size:92px;font-weight:600;color:rgba(0,0,0,.18);line-height:90px}
.wine-row{position:absolute;top:1634px;width:267px;height:181px;background:linear-gradient(180deg,#e8e8e8,#d6d6d6)}

/* products */
.product-grid{position:absolute;left:127px;top:1898px;width:946px;height:305px;border:1px solid var(--line);display:flex}
.product{flex:1;border-right:1px solid var(--line);text-align:center;padding-top:22px;position:relative}
.product:last-child{border-right:0}
.product h3{font-weight:500;font-size:14px;line-height:17px;color:#444}
.product.featured h3{color:var(--green)}
.product .cat{font-size:9px;color:var(--muted);margin-top:9px}
.product .thumb{width:170px;height:170px;background:#e6e6e6;margin:12px auto 0}
.product.featured .thumb{background:#f7f7f7}
.product .price{font-size:16px;font-weight:600;color:var(--green);margin-top:11px}
.bag-btn{left:66px;top:142px;width:106px;height:32px;line-height:32px;font-size:10px;letter-spacing:0}
.wish{position:absolute;left:0;width:100%;top:195px;font-size:10px;color:var(--muted)}
.mini-list{position:absolute;left:127px;top:2218px;width:462px;height:98px;border:1px solid var(--line)}
.mini{position:absolute;top:16px;display:flex;gap:14px}
.mini .thumb{width:64px;height:64px;background:#e6e6e6}
.mini .cat{font-size:9px;color:var(--muted);margin-top:11px}
.mini .name{font-size:13px;color:#333;margin-top:2px}
.mini .price{font-size:10px;color:var(--green);font-weight:600;margin-top:3px}
.mini .price s{color:#aaa;font-weight:400;margin-right:4px}
.feature-card{position:absolute;left:612px;top:2218px;width:461px;height:98px;background:var(--panel);padding:18px 0 0 25px}
.feature-card .cat{font-size:9px;color:var(--muted);display:flex;align-items:center;gap:8px}
.feature-card .cat::before{content:"";width:16px;height:2px;background:var(--green)}
.feature-card .name{font-size:17px;color:#444;margin-top:10px}
.feature-card .price{font-size:12px;font-weight:600;color:var(--green);margin-top:12px}

/* video */
.video-head{position:absolute;left:0;width:1200px;top:2460px;text-align:center}
.video-head h2{font-weight:500;font-size:36px;color:#444}
.video-head .kicker{margin-top:6px}
.video-deco{position:absolute;left:563px;top:2390px;width:75px;height:80px;background:linear-gradient(180deg,#e9ece4,#cfd8c5);opacity:.7}
.video{position:absolute;left:127px;top:2543px;width:946px;height:474px;background:radial-gradient(circle at 50% 40%,#a8b94a 0%,#6f8e22 40%,#3a2a12 100%)}
.video-label{position:absolute;left:27px;top:22px;color:var(--white);font-size:14px;font-weight:500}
.play{position:absolute;left:420px;top:194px}
.controls{position:absolute;left:0;bottom:0;width:946px;height:32px;background:rgba(0,0,0,.55)}
.controls .buffer{position:absolute;left:34px;top:0;width:125px;height:32px;background:#c08e6b}
.controls .time{position:absolute;top:10px;color:var(--white);font-size:10px}
.controls .marker{position:absolute;left:302px;top:-8px;width:1px;height:40px;background:rgba(255,255,255,.5)}

/* contact */
.contact{position:absolute;left:0;top:3017px;width:1200px;height:183px}
.contact-col{position:absolute;top:36px;width:300px;text-align:center}
.contact-col h4{font-weight:500;font-size:15px;margin-top:14px;color:#444}
.contact-col .val{margin-top:18px;font-size:17px;color:#333}
.contact-col .addr{margin-top:18px;font-size:13px;line-height:22px;color:#333}
.contact-col .mail{margin-top:18px;font-size:13px;color:var(--green)}
.site-footer{position:absolute;left:0;top:3200px;width:1200px;height:55px;border-top:1px solid var(--line)}
.site-footer .rights{position:absolute;left:163px;top:22px;font-size:9px;color:#b5b5b5}
.social-foot{position:absolute;right:165px;top:22px;display:flex;gap:34px}
.social-foot i{background:#bdbdbd}
</style>
</head>
<body>

<header class="site-header">
  <div class="brand"><span class="brand-dot"></span>Genussfahrten</div>
  <div class="social-top"><i></i><i></i><i></i></div>
  <nav class="main-nav">
    <span>HOME</span><span class="sep">~</span><span>SERVICE</span><span class="sep">~</span><span>INFORMATIONEN</span><span class="sep">~</span><span>ONLINESHOP</span><span class="sep">~</span><span>CONTACT</span>
  </nav>
</header>

<section class="hero" role="img" aria-label="Weinberge und Hügellandschaft der Südsteiermark im Abendlicht">
  <h1 class="hero-title">Genussfahrten</h1>
  <div class="hero-rule"></div>
  <p class="hero-text">Quisque rutrum. Aenean imperdiet. Etiam ultricies nisi vel augue. Curabitur ullamcorper ultricies nisi. Nam eget dui. Etiam rhoncus.</p>
  <div class="hero-btn">ONLINESHOP</div>
</section>

<svg class="hero-badge" viewBox="0 0 80 72" aria-hidden="true">
  <path d="M40 2 L76 16 L76 52 L40 70 L4 52 L4 16 Z" fill="#f6f5f1" stroke="#dcdcd4"/>
  <circle cx="40" cy="34" r="22" fill="#fff" stroke="#3d6b0a" stroke-width="1.5"/>
  <circle cx="40" cy="34" r="10" fill="none" stroke="#3d6b0a" stroke-width="1.5"/>
</svg>

<section class="about">
  <h2>Über uns</h2>
  <div class="kicker">WE CREATE DELICIOUS MEMORIES</div>
  <div class="about-text">
    <p>Wir sind ein Start-up Unternehmen mit Sitz in Berlin und möchten unsere Begeisterung für die Steiermark mit ihren kulinarischen Spezialitäten, wunderschönen Landschaften und gastfreundlichen Menschen mit unseren Gästen teilen. Wir glauben, dass unsere Reisen hervorragende Möglichkeiten zum Entspannen und Genießen bieten und sich deshalb besonders gut als „Genussreise“ für umsatzstarke Kunden, erfolgreiche Mitarbeiter oder einfach als private Kurzreise mit Freunden eignen.</p>
    <p>Während Marketing und Vertrieb in Berlin angesiedelt sind, werden die Reisen selbst durch einen ortsansässigen Steirer durchgeführt. Dadurch können wir beste Qualität garantieren und auf Veränderungen flexibel reagieren. Unsere Partner sind ausgesuchte Hotels, Restaurants mit besonders guter Küche und Winzer der Spitzenklasse.</p>
    <p>Durch die kleine Gruppengröße von maximal 8 Personen können wir exklusiven Service bieten.</p>
  </div>
  <div class="collage">
    <div class="tile a" role="img" aria-label="Blaue Weintrauben am Rebstock"></div>
    <div class="tile b" role="img" aria-label="Zwei Gläser Rotwein vor grünem Hintergrund"></div>
    <div class="tile c" role="img" aria-label="Rotwein wird ins Glas gegossen"></div>
    <div class="tile d" role="img" aria-label="Weiße Trauben zwischen Weinlaub"></div>
    <div class="tastes">TASTES SO<br>GOOD!</div>
  </div>
</section>

<section class="collection-banner" role="img" aria-label="Zwei Rotweingläser und Trauben auf einem Holztisch im Grünen">
  <div class="banner-title"><small>2018</small> New<br>Collections</div>
  <div class="banner-sub">Your can put your own text here!</div>
  <div class="btn-green banner-btn">SHOP NOW</div>
</section>
<div class="collection-list">
  <div class="collection-item">The new collection of<br>best wine</div>
  <div class="collection-item active"><span class="num">02</span>2018 Collection<br>Your own text here!</div>
  <div class="collection-item">Sale of the day! Discounts<br>of 20 to 50% on all products</div>
  <div class="collection-item">New items of the summer<br>Your own text here</div>
</div>
<div class="wine-row" style="left:127px" role="img" aria-label="Vier Rotweinflaschen nebeneinander"></div>
<div class="wine-row" style="left:468px" role="img" aria-label="Vier Rotweinflaschen nebeneinander"></div>
<div class="wine-row" style="left:806px" role="img" aria-label="Vier Rotweinflaschen nebeneinander"></div>

<section class="product-grid">
  <div class="product"><h3>The Name of the<br>Wine</h3><div class="cat">Category</div><div class="thumb"></div><div class="price">$124</div></div>
  <div class="product featured"><h3>The Name of the<br>Wine</h3><div class="cat">Category</div><div class="thumb"></div><div class="price">$76</div>
    <div class="btn-green bag-btn">Add to Bag &nbsp;›</div>
    <div class="wish">♥ &nbsp;Add to wishlist</div></div>
  <div class="product"><h3>The Name of the<br>Wine</h3><div class="cat">Category</div><div class="thumb"></div><div class="price">$92</div></div>
  <div class="product"><h3>The Name of the<br>Wine</h3><div class="cat">Category</div><div class="thumb"></div><div class="price">$117</div></div>
</section>
<div class="mini-list">
  <div class="mini" style="left:17px"><div class="thumb"></div><div><div class="cat">Category</div><div class="name">Red Wine</div><div class="price"><s>$83</s>$66</div></div></div>
  <div class="mini" style="left:243px"><div class="thumb"></div><div><div class="cat">Category</div><div class="name">White Wine</div><div class="price">$48</div></div></div>
</div>
<div class="feature-card"><div class="cat">Category</div><div class="name">The Name of the Wine</div><div class="price">$148</div></div>

<div class="video-deco" role="img" aria-label="Zarte Illustration einer Windmühle"></div>
<div class="video-head"><h2>The Main Video Here</h2><div class="kicker">THE BEST WINE YOU'VE EVER TASTED!</div></div>
<section class="video" role="img" aria-label="Videostandbild: Rotweinflasche, zwei Gläser und Trauben auf einem Fass">
  <div class="video-label">Creative world space</div>
  <svg class="play" width="106" height="106" viewBox="0 0 106 106" aria-hidden="true"><circle cx="53" cy="53" r="51" fill="none" stroke="#fff" stroke-width="2"/><path d="M45 40 L68 53 L45 66 Z" fill="#fff"/></svg>
  <div class="controls">
    <svg class="abs" style="left:12px;top:10px" width="12" height="12" viewBox="0 0 12 12"><path d="M2 1 L11 6 L2 11 Z" fill="#fff"/></svg>
    <div class="buffer"></div>
    <div class="marker"></div>
    <div class="time" style="left:294px;top:-20px">9:37</div>
    <div class="time" style="left:835px">15:00</div>
    <svg class="abs" style="left:893px;top:10px" width="12" height="12" viewBox="0 0 12 12"><path d="M1 4 H4 L8 1 V11 L4 8 H1 Z" fill="#fff"/></svg>
    <svg class="abs" style="left:925px;top:10px" width="12" height="12" viewBox="0 0 12 12" fill="none" stroke="#fff" stroke-width="1.5"><path d="M1 4V1H4M8 1H11V4M11 8V11H8M4 11H1V8"/></svg>
  </div>
</section>

<section class="contact">
  <div class="contact-col" style="left:146px">
    <svg width="26" height="42" viewBox="0 0 26 42" fill="none" stroke="#3d6b0a" stroke-width="1.5"><rect x="1" y="1" width="24" height="40" rx="3"/><path d="M1 7H25M1 34H25"/><circle cx="13" cy="38" r="1.2"/></svg>
    <h4>Call us</h4><div class="val">+49 170 5550182</div>
  </div>
  <div class="contact-col" style="left:446px">
    <svg width="30" height="40" viewBox="0 0 30 40" fill="none" stroke="#3d6b0a" stroke-width="1.5"><path d="M15 38 C6 26 2 20 2 14 A13 13 0 0 1 28 14 C28 20 24 26 15 38 Z"/><circle cx="15" cy="14" r="5"/></svg>
    <h4>Location</h4><div class="addr">Genussfahrten Marlene Vogt<br>Lindenweg 12, 10115 Berlin</div>
  </div>
  <div class="contact-col" style="left:746px">
    <svg width="44" height="32" viewBox="0 0 44 32" fill="none" stroke="#3d6b0a" stroke-width="1.5"><rect x="1" y="1" width="42" height="30"/><path d="M1 1 L22 18 L43 1"/></svg>
    <h4>Mail</h4><div class="mail">kontakt@genussfahrten.de</div>
  </div>
</section>

<footer class="site-footer">
  <div class="rights">All rights reserved</div>
  <div class="social-foot"><i></i><i></i><i></i></div>
</footer>

</body>
</html>
```